Business Card - Tidal Lanes

Need Business Card design for company named Tidal Lanes. Software development focused mainly on Brindle Orvix & Zelt Apps. I've attached our logo with both a black and white background. Please add trademark symbol to logo when using.

```html
<!DOCTYPE html>
<html lang="en">
<head>
<meta charset="utf-8">
<title>Tidal Lanes – Business Card</title>
<link rel="stylesheet" href="https://fonts.googleapis.com/css2?family=Open+Sans:wght@400;600;700&display=swap">
<style>
  :root {
    --page: #e8e5e0;
    --card-dark: #0b0b0c;
    --card-dark-sheen: #26272a;
    --card-light: #ffffff;
    --text-light: #f2f2f2;
    --text-dark: #3a3a3c;
    --brand-red: #d9202a;
    --brand-orange: #f39a3c;
    --brand-yellow: #f6c21c;
  }
  * { box-sizing: border-box; margin: 0; padding: 0; }
  html, body {
    width: 1200px;
    height: 1014px;
    overflow: hidden;
    background: var(--page);
    font-family: "Open Sans", Arial, sans-serif;
  }
  .canvas {
    position: relative;
    width: 1200px;
    height: 1014px;
  }
  .card {
    position: absolute;
    left: 250px;
    width: 700px;
    height: 400px;
    box-shadow: 0 10px 28px rgba(0,0,0,0.22);
    overflow: hidden;
  }
  .card--front {
    top: 70px;
    background: linear-gradient(160deg, var(--card-dark) 55%, var(--card-dark-sheen) 100%);
  }
  .card--back {
    top: 540px;
    background: var(--card-light);
  }
  .corner-dot {
    position: absolute;
    left: -30px;
    top: 44px;
    width: 60px;
    height: 60px;
    border-radius: 50%;
    background: var(--brand-red);
  }
  .contact {
    position: absolute;
    left: 62px;
    top: 40px;
    color: var(--text-light);
  }
  .contact__name {
    font-size: 30px;
    font-weight: 700;
    line-height: 1.1;
  }
  .contact__role {
    font-size: 23px;
    font-weight: 600;
    color: var(--brand-red);
    margin-bottom: 26px;
  }
  .contact__line {
    font-size: 19px;
    line-height: 1.55;
  }
  .contact__label { color: var(--brand-yellow); }
  .contact__web {
    margin-top: 4px;
    font-size: 23px;
    font-weight: 700;
    color: var(--brand-red);
  }
  .brand {
    position: absolute;
    inset: 0;
    display: flex;
    align-items: center;
    justify-content: center;
    gap: 18px;
  }
  .brand__dot {
    width: 38px;
    height: 38px;
    border-radius: 50%;
    background: var(--brand-orange);
  }
  .brand__name {
    font-size: 46px;
    font-weight: 700;
    color: var(--text-dark);
    letter-spacing: -1px;
  }
  .brand__tm { font-size: 16px; vertical-align: super; }
</style>
</head>
<body>
<main class="canvas">
  <section class="card card--front" aria-label="Card front">
    <span class="corner-dot"></span>
    <div class="contact">
      <p class="contact__name">Dorian Kessler</p>
      <p class="contact__role">Manager</p>
      <p class="contact__line">555-214-7730 <span class="contact__label">Mobile</span></p>
      <p class="contact__line">dorian@tidallanes.com</p>
      <p class="contact__line">4120 Harbor Row</p>
      <p class="contact__line">Marlow, FL 30412</p>
      <p class="contact__line">555-308-1946 <span class="contact__label">Fax</span></p>
      <p class="contact__web">tidallanes.com</p>
    </div>
  </section>

  <section class="card card--back" aria-label="Card back">
    <div class="brand">
      <span class="brand__dot"></span>
      <span class="brand__name">Tidal Lanes<span class="brand__tm">™</span></span>
    </div>
  </section>
</main>
</body>
</html>
```